Tidewell Comforts, a portable luxury restroom trailer company needs a landing page

We need a landing page for a luxury portable restroom trailer company. This should be modern, and simple - use any combination of Pantone colors: Warm Gray 1C, Black 7C, 7529c, 873C, 8003C

We rent these trailers for special events like weddings, private parties, festivals, family reunions, team building, wine tastings, beer tastings, food truck round-ups, etc.

An idea of the landing page is in the files below. Please use stock photography and placeholder text for now. The winning design will be given final content.

Requirements
Must have
• Multiple "Get Quote" buttons or a place for them to type in type of rental, how many people etc

```html
<!DOCTYPE html>
<html lang="en">
<head>
<meta charset="utf-8">
<title>Tidewell Comforts — Luxury Restroom Trailers</title>
<link rel="stylesheet" href="https://fonts.googleapis.com/css2?family=Cinzel:wght@400;600;700&family=Libre+Baskerville:ital@0;1&family=Montserrat:ital,wght@0,400;0,500;0,600;1,400&display=swap">
<style>
:root{
  --cyan:#3bc6f2;
  --cyan-soft:rgba(59,198,242,.82);
  --navy:#0e5b87;
  --navy-deep:#0b2d4d;
  --ink:#1b1b1b;
  --warm-gray:#e9e8e6;
  --taupe:#8e857b;
  --taupe-light:#cbc5bd;
  --slate:#5d5f61;
  --footer:#2b2b2b;
  --white:#ffffff;
}
*{box-sizing:border-box;margin:0;padding:0}
html,body{width:1200px;height:3495px;overflow:hidden}
body{position:relative;background:var(--white);font-family:'Montserrat',sans-serif;color:var(--ink)}
.abs{position:absolute}
.photo{position:absolute;display:block}

/* header */
.site-header{position:absolute;left:0;top:0;width:1200px;height:65px;background:var(--white);border-top:4px solid var(--cyan)}
.brand{position:absolute;left:111px;top:18px;font-family:'Cinzel',serif;font-size:26px;letter-spacing:1px;color:var(--ink)}
.nav{position:absolute;top:24px;font-family:'Libre Baskerville',serif;font-size:14px;color:var(--ink)}
.nav-phone{position:absolute;left:836px;top:25px;font-size:12px;color:var(--ink);display:flex;align-items:center;gap:6px}
.social{position:absolute;display:flex;gap:6px}
.social span{display:block;width:28px;height:28px;background:#333}

/* hero */
.hero{position:absolute;left:0;top:65px;width:1200px;height:683px;background:var(--warm-gray)}
.hero-title{position:absolute;left:681px;top:130px;font-family:'Cinzel',serif;font-size:40px;letter-spacing:2px;color:var(--ink)}
.hero-copy{position:absolute;left:350px;top:636px;width:290px;text-align:center;font-size:12.5px;font-style:italic;line-height:19.5px;color:#333}
.bar{position:absolute}
.tape{position:absolute;background:var(--cyan-soft);transform-origin:center}

/* section headings */
.section-title{position:absolute;left:0;width:1200px;display:flex;justify-content:center;align-items:center;gap:12px;font-family:'Cinzel',serif;font-size:40px;color:var(--ink)}
.rule{width:88px;height:20px}

/* events */
.event-card{position:absolute;top:1009px;width:223px;height:277px;border-radius:6px;overflow:hidden;box-shadow:0 4px 10px rgba(0,0,0,.25)}
.event-card .shade{position:absolute;inset:0;background:linear-gradient(to bottom,rgba(0,0,0,0) 55%,rgba(0,0,0,.85))}
.event-name{position:absolute;left:0;width:100%;top:215px;text-align:center;font-family:'Cinzel',serif;font-size:19px;letter-spacing:1px;color:var(--white)}
.learn{position:absolute;left:0;width:100%;top:248px;display:flex;justify-content:center;align-items:center;gap:8px;font-family:'Cinzel',serif;font-size:11px;font-style:italic;color:var(--cyan);text-decoration:underline}
.learn i{display:inline-flex;width:24px;height:24px;border:1.5px solid var(--white);border-radius:50%;align-items:center;justify-content:center}
.btn-cyan{position:absolute;background:var(--cyan);color:var(--white);font-family:'Cinzel',serif;font-size:16px;display:flex;align-items:center;justify-content:center;box-shadow:0 8px 14px rgba(0,0,0,.18)}

/* products */
.products{position:absolute;left:0;top:1465px;width:1200px;height:1030px;background:var(--cyan)}
.product-card{position:absolute;width:309px;height:382px;background:var(--white);border-radius:6px}
.product-name{position:absolute;left:0;width:100%;top:260px;text-align:center;font-family:'Cinzel',serif;font-size:20px;letter-spacing:1px;color:var(--ink)}
.product-actions{position:absolute;left:28px;top:316px;width:253px;height:37px;display:flex;border:1px solid var(--navy)}
.product-actions span{flex:1;display:flex;align-items:center;justify-content:center;font-family:'Cinzel',serif;font-weight:700;font-size:13px}
.act-view{background:var(--navy);color:var(--white)}
.act-demo{color:var(--navy)}

/* contact */
.contact-bg{position:absolute;left:0;top:2640px;width:1200px;height:509px;background:linear-gradient(to bottom,#fff 0%,#f1f1f0 30%,#c9c6c2 70%,#8a7f78 100%)}
.form-card{position:absolute;left:194px;top:2666px;width:830px;height:392px;background:var(--white);border-radius:30px;box-shadow:0 0 18px rgba(0,0,0,.12)}
.field{position:absolute;width:354px;height:43px;border:1px solid #8a8a8a;border-radius:22px;display:flex;align-items:center;justify-content:space-between;padding:0 14px 0 19px;font-family:'Libre Baskerville',serif;font-size:13px;color:#7a7a7a}
.field svg{width:16px;height:16px}

/* footer */
.site-footer{position:absolute;left:0;top:3149px;width:1200px;height:346px;background:var(--footer);color:var(--white)}
.foot-brand{position:absolute;left:0;width:626px;top:102px;text-align:center;font-family:'Cinzel',serif;font-size:26px;letter-spacing:1px}
.foot-head{position:absolute;top:80px;font-family:'Cinzel',serif;font-size:20px;color:var(--cyan)}
.foot-list{position:absolute;top:126px;list-style:none;font-size:12px;line-height:24.5px}
.foot-list li::before{content:"»";color:var(--cyan);margin-right:8px;font-size:14px}
.foot-rule{position:absolute;left:111px;top:282px;width:976px;height:1px;background:#555}
.copyright{position:absolute;left:0;width:1200px;top:298px;text-align:center;font-family:'Cinzel',serif;font-size:13px;color:var(--white)}
.to-top{position:absolute;left:1119px;top:3388px;width:40px;height:40px;border-radius:50%;background:var(--cyan);display:flex;align-items:center;justify-content:center}
</style>
</head>
<body>

<header class="site-header">
  <div class="brand">Tidewell Comforts</div>
  <a class="nav" style="left:584px">Events</a>
  <a class="nav" style="left:666px">Products</a>
  <a class="nav" style="left:765px">Contact</a>
  <div class="nav-phone">
    <svg width="14" height="14" viewBox="0 0 24 24"><path fill="#3bc6f2" d="M6.6 10.8a15.2 15.2 0 0 0 6.6 6.6l2.2-2.2a1 1 0 0 1 1-.25 11.4 11.4 0 0 0 3.6.57 1 1 0 0 1 1 1V20a1 1 0 0 1-1 1A17 17 0 0 1 3 4a1 1 0 0 1 1-1h3.5a1 1 0 0 1 1 1c0 1.25.2 2.45.57 3.57a1 1 0 0 1-.25 1z"/></svg>
    +1 (555) 014 2290
  </div>
  <div class="social" style="left:990px;top:19px"><span></span><span></span><span></span></div>
</header>

<section class="hero">
</section>
<!-- hero collage -->
<div class="bar" style="left:384px;top:123px;width:233px;height:11px;background:var(--taupe)"></div>
<div class="bar" style="left:384px;top:144px;width:200px;height:9px;background:var(--taupe-light)"></div>
<h1 class="hero-title">Tidewell Comforts</h1>

<div class="photo" role="img" aria-label="White luxury restroom trailer with steps" style="left:106px;top:123px;width:259px;height:345px;background:linear-gradient(135deg,#f4f5f6,#c9ccd0 70%,#9ea3a8)"></div>
<div class="photo" role="img" aria-label="Restroom trailer parked on gravel" style="left:384px;top:168px;width:280px;height:193px;background:linear-gradient(160deg,#ececec,#cfcfcf 60%,#7b7b7b)"></div>
<div class="photo" role="img" aria-label="Large restroom trailer outside a warehouse" style="left:664px;top:197px;width:300px;height:229px;background:linear-gradient(180deg,#bfc2c4,#dfe0e1 55%,#6e6e6e)"></div>
<div class="photo" role="img" aria-label="Outdoor ceremony chairs in a field" style="left:964px;top:229px;width:182px;height:293px;background:linear-gradient(180deg,#b9bdb6 0%,#8a7a5a 35%,#5d5a3f 70%,#2f3a2e)"></div>
<div class="photo" role="img" aria-label="Guests dining at a long outdoor table" style="left:113px;top:485px;width:193px;height:193px;background:linear-gradient(180deg,#e9ecec,#9aa483 50%,#5a4d3a)"></div>
<div class="photo" role="img" aria-label="Semi truck hauling a restroom trailer" style="left:321px;top:370px;width:357px;height:229px;background:linear-gradient(180deg,#f1efeb 0%,#dcd7cf 45%,#b7a48c 80%,#c9b69a)"></div>
<div class="photo" role="img" aria-label="Floral wedding arch on a terrace" style="left:675px;top:428px;width:229px;height:232px;background:linear-gradient(180deg,#a9c49a,#eef0ef 45%,#cfd3d5)"></div>
<div class="photo" role="img" aria-label="Restroom trailer at a rustic venue" style="left:716px;top:591px;width:255px;height:212px;background:linear-gradient(170deg,#9a5a45,#eeeeee 45%,#6f6a63)"></div>
<div class="photo" role="img" aria-label="Candle and flower table centrepiece" style="left:991px;top:593px;width:136px;height:231px;background:linear-gradient(180deg,#c9cfbf,#f3ece9 55%,#e8b9c2)"></div>

<div class="bar" style="left:918px;top:541px;width:232px;height:10px;background:var(--slate)"></div>
<div class="bar" style="left:918px;top:559px;width:201px;height:11px;background:var(--navy)"></div>
<div class="bar" style="left:134px;top:692px;width:172px;height:9px;background:var(--navy)"></div>
<div class="bar" style="left:144px;top:715px;width:162px;height:9px;background:var(--navy)"></div>
<div class="bar" style="left:76px;top:735px;width:230px;height:11px;background:var(--navy-deep)"></div>

<div class="tape" style="left:38px;top:140px;width:200px;height:40px;transform:rotate(-45deg)"></div>
<div class="tape" style="left:575px;top:604px;width:230px;height:44px;transform:rotate(42deg)"></div>
<div class="tape" style="left:948px;top:560px;width:200px;height:38px;transform:rotate(-30deg)"></div>

<p class="hero-copy">Perspiciatis undelk omnis iste natus error sit voluptatem accusantiu seoijism doloremque laudantium, totam rems aperiam, eaque ipsa quae lkseij abillo.</p>

<!-- events -->
<h2 class="section-title" style="top:915px">
  <svg class="rule" viewBox="0 0 88 20"><rect x="0" y="15" width="88" height="3" fill="#0e5b87"/><rect x="40" y="5" width="48" height="3" fill="#0e5b87"/></svg>
  Events
  <svg class="rule" viewBox="0 0 88 20"><rect x="0" y="15" width="88" height="3" fill="#0e5b87"/><rect x="0" y="5" width="48" height="3" fill="#0e5b87"/></svg>
</h2>

<article class="event-card" style="left:111px">
  <div class="photo" role="img" aria-label="White gazebo in a garden" style="inset:0;background:linear-gradient(180deg,#32402b,#5f6a55 45%,#c8c6bf 70%,#3b3d33)"></div>
  <div class="shade"></div>
  <div class="event-name">Weddings</div>
  <div class="learn">Learn More <i><svg width="10" height="10" viewBox="0 0 10 10"><path d="M3 1l4 4-4 4" stroke="#fff" stroke-width="1.6" fill="none"/></svg></i></div>
</article>
<article class="event-card" style="left:362px">
  <div class="photo" role="img" aria-label="Candlelit dinner party table" style="inset:0;background:linear-gradient(180deg,#5a3a2a,#a36b4d 40%,#d8cdc2 70%,#3a2a22)"></div>
  <div class="shade"></div>
  <div class="event-name">Private Parties</div>
  <div class="learn">Learn More <i><svg width="10" height="10" viewBox="0 0 10 10"><path d="M3 1l4 4-4 4" stroke="#fff" stroke-width="1.6" fill="none"/></svg></i></div>
</article>
<article class="event-card" style="left:614px">
  <div class="photo" role="img" aria-label="Festival crowd with confetti" style="inset:0;background:linear-gradient(180deg,#8fc3e6,#c9a59b 40%,#b3526b 70%,#2a2330)"></div>
  <div class="shade"></div>
  <div class="event-name">Festivals</div>
  <div class="learn">Learn More <i><svg width="10" height="10" viewBox="0 0 10 10"><path d="M3 1l4 4-4 4" stroke="#fff" stroke-width="1.6" fill="none"/></svg></i></div>
</article>
<article class="event-card" style="left:866px">
  <div class="photo" role="img" aria-label="Family gathered outdoors" style="inset:0;background:linear-gradient(180deg,#cfd6c7,#8b7361 45%,#5b3d37 75%,#231a18)"></div>
  <div class="shade"></div>
  <div class="event-name">Family Reunions</div>
  <div class="learn">Learn More <i><svg width="10" height="10" viewBox="0 0 10 10"><path d="M3 1l4 4-4 4" stroke="#fff" stroke-width="1.6" fill="none"/></svg></i></div>
</article>

<a class="btn-cyan" style="left:511px;top:1326px;width:178px;height:45px">View More</a>

<!-- products -->
<section class="products"></section>
<h2 class="section-title" style="top:1540px">
  <svg class="rule" viewBox="0 0 88 20"><rect x="0" y="15" width="88" height="3" fill="#0e5b87"/><rect x="40" y="5" width="48" height="3" fill="#0e5b87"/></svg>
  Products
  <svg class="rule" viewBox="0 0 88 20"><rect x="0" y="15" width="88" height="3" fill="#0e5b87"/><rect x="0" y="5" width="48" height="3" fill="#0e5b87"/></svg>
</h2>

<article class="product-card" style="left:111px;top:1611px">
  <div class="photo" role="img" aria-label="Towable restroom trailer" style="left:28px;top:28px;width:270px;height:200px;background:linear-gradient(135deg,#f1f2f3,#c6c8ca 65%,#8d8f92)"></div>
  <div class="product-name">Ksoieosdeu Saleiuise</div>
  <div class="product-actions"><span class="act-view">View Product</span><span class="act-demo">Quick Demo</span></div>
</article>
<article class="product-card" style="left:446px;top:1611px">
  <div class="photo" role="img" aria-label="Restroom truck" style="left:0;top:45px;width:309px;height:165px;background:linear-gradient(180deg,#e4e5e6,#c1c3c5 65%,#3a3a3a)"></div>
  <div class="product-name">Ksoieosdeu Saleiuise</div>
  <div class="product-actions"><span class="act-view">View Product</span><span class="act-demo">Quick Demo</span></div>
</article>
<article class="product-card" style="left:780px;top:1611px">
  <div class="photo" role="img" aria-label="Semi truck with restroom trailer" style="left:6px;top:78px;width:303px;height:97px;background:linear-gradient(180deg,#e6ded2,#cfc2ae 60%,#3d3a36)"></div>
  <div class="product-name">Ksoieosdeu Saleiuise</div>
  <div class="product-actions"><span class="act-view">View Product</span><span class="act-demo">Quick Demo</span></div>
</article>
<article class="product-card" style="left:111px;top:2019px">
  <div class="photo" role="img" aria-label="Semi truck with restroom trailer" style="left:0;top:104px;width:309px;height:97px;background:linear-gradient(180deg,#e6ded2,#cfc2ae 60%,#3d3a36)"></div>
  <div class="product-name">Ksoieosdeu Saleiuise</div>
  <div class="product-actions"><span class="act-view">View Product</span><span class="act-demo">Quick Demo</span></div>
</article>
<article class="product-card" style="left:446px;top:2019px">
  <div class="photo" role="img" aria-label="Restroom truck" style="left:4px;top:50px;width:305px;height:165px;background:linear-gradient(180deg,#e4e5e6,#c1c3c5 65%,#3a3a3a)"></div>
  <div class="product-name">Ksoieosdeu Saleiuise</div>
  <div class="product-actions"><span class="act-view">View Product</span><span class="act-demo">Quick Demo</span></div>
</article>
<article class="product-card" style="left:780px;top:2019px">
  <div class="photo" role="img" aria-label="Towable restroom trailer" style="left:16px;top:20px;width:275px;height:210px;background:linear-gradient(225deg,#f1f2f3,#c6c8ca 65%,#8d8f92)"></div>
  <div class="product-name">Ksoieosdeu Saleiuise</div>
  <div class="product-actions"><span class="act-view">View Product</span><span class="act-demo">Quick Demo</span></div>
</article>

<!-- contact -->
<h2 class="section-title" style="top:2570px">
  <svg class="rule" viewBox="0 0 88 20"><rect x="0" y="15" width="88" height="3" fill="#0e5b87"/><rect x="40" y="5" width="48" height="3" fill="#0e5b87"/></svg>
  Contact Us
  <svg class="rule" viewBox="0 0 88 20"><rect x="0" y="15" width="88" height="3" fill="#0e5b87"/><rect x="0" y="5" width="48" height="3" fill="#0e5b87"/></svg>
</h2>
<div class="contact-bg" role="img" aria-label="Faded interior of a restroom trailer"></div>

<form class="form-card">
  <label class="field" style="left:53px;top:45px">Full Name
    <svg viewBox="0 0 16 16"><circle cx="8" cy="5" r="3" fill="none" stroke="#3bc6f2" stroke-width="1.2"/><path d="M2 15c0-3.5 2.7-5 6-5s6 1.5 6 5z" fill="none" stroke="#3bc6f2" stroke-width="1.2"/></svg></label>
  <label class="field" style="left:422px;top:45px">Where
    <svg viewBox="0 0 16 16"><path d="M8 1a5 5 0 0 1 5 5c0 4-5 9-5 9S3 10 3 6a5 5 0 0 1 5-5z" fill="#3bc6f2"/><circle cx="8" cy="6" r="1.8" fill="#fff"/></svg></label>
  <label class="field" style="left:53px;top:106px">Phone
    <svg viewBox="0 0 24 24"><path fill="#3bc6f2" d="M6.6 10.8a15.2 15.2 0 0 0 6.6 6.6l2.2-2.2a1 1 0 0 1 1-.25 11.4 11.4 0 0 0 3.6.57 1 1 0 0 1 1 1V20a1 1 0 0 1-1 1A17 17 0 0 1 3 4a1 1 0 0 1 1-1h3.5a1 1 0 0 1 1 1c0 1.25.2 2.45.57 3.57a1 1 0 0 1-.25 1z"/></svg></label>
  <label class="field" style="left:422px;top:106px">Email
    <svg viewBox="0 0 16 16"><rect x="1" y="3" width="14" height="10" rx="1" fill="#3bc6f2"/><path d="M1.5 4l6.5 5 6.5-5" stroke="#fff" stroke-width="1.2" fill="none"/></svg></label>
  <label class="field" style="left:53px;top:166px">Type of Event?
    <svg viewBox="0 0 16 16"><path d="M4 6l4 4 4-4" stroke="#444" stroke-width="1.5" fill="none"/></svg></label>
  <label class="field" style="left:422px;top:166px">How Many People?
    <svg viewBox="0 0 16 16"><circle cx="8" cy="5" r="3" fill="none" stroke="#3bc6f2" stroke-width="1.2"/><path d="M2 15c0-3.5 2.7-5 6-5s6 1.5 6 5z" fill="none" stroke="#3bc6f2" stroke-width="1.2"/></svg></label>
  <label class="field" style="left:53px;top:225px">When Do You Need It?
    <svg viewBox="0 0 16 16"><rect x="2" y="3" width="12" height="11" rx="1" fill="none" stroke="#3bc6f2" stroke-width="1.2"/><path d="M2 6.5h12M5 1.5v3M11 1.5v3" stroke="#3bc6f2" stroke-width="1.2"/></svg></label>
  <label class="field" style="left:422px;top:225px">For How Long?
    <svg viewBox="0 0 16 16"><circle cx="8" cy="8" r="6.3" fill="none" stroke="#3bc6f2" stroke-width="1.2"/><path d="M8 4.5V8l2.5 1.5" stroke="#3bc6f2" stroke-width="1.2" fill="none"/></svg></label>
  <a class="btn-cyan" style="left:333px;top:301px;width:180px;height:46px">Submit</a>
</form>

<!-- footer -->
<footer class="site-footer">
  <div class="foot-brand">Tidewell Comforts</div>
  <div class="social" style="left:263px;top:146px"><span style="background:var(--cyan)"></span><span style="background:var(--cyan)"></span><span style="background:var(--cyan)"></span></div>
  <div class="abs" style="left:300px;top:193px;width:26px;height:2px;background:var(--cyan)"></div>
  <div class="abs" style="left:0;width:626px;top:206px;display:flex;justify-content:center;align-items:center;gap:8px;font-size:17px;font-weight:500">
    <svg width="17" height="17" viewBox="0 0 24 24"><path fill="#3bc6f2" d="M6.6 10.8a15.2 15.2 0 0 0 6.6 6.6l2.2-2.2a1 1 0 0 1 1-.25 11.4 11.4 0 0 0 3.6.57 1 1 0 0 1 1 1V20a1 1 0 0 1-1 1A17 17 0 0 1 3 4a1 1 0 0 1 1-1h3.5a1 1 0 0 1 1 1c0 1.25.2 2.45.57 3.57a1 1 0 0 1-.25 1z"/></svg>
    +1 (555) 014 2290
  </div>

  <div class="foot-head" style="left:525px">Quick Links</div>
  <div class="abs" style="left:525px;top:111px;width:26px;height:2px;background:var(--cyan)"></div>
  <ul class="foot-list" style="left:525px"><li>Events</li><li>Products</li><li>Contact</li></ul>

  <div class="foot-head" style="left:721px">Links</div>
  <div class="abs" style="left:721px;top:111px;width:26px;height:2px;background:var(--cyan)"></div>
  <ul class="foot-list" style="left:721px"><li>Copyright</li><li>Legal</li><li>Privacy</li><li>Accessibility</li><li>Sitemap</li></ul>

  <div class="foot-head" style="left:877px">Support</div>
  <div class="abs" style="left:877px;top:111px;width:26px;height:2px;background:var(--cyan)"></div>
  <ul class="foot-list" style="left:877px"><li>Faq's</li><li>Terms &amp; Conditions</li><li>Privacy Policy</li><li>Site Map</li><li>Cookies Policy</li></ul>

  <div class="foot-rule"></div>
  <div class="copyright">Copyright © 2022. All rights reserved.</div>
</footer>
<a class="to-top"><svg width="16" height="16" viewBox="0 0 16 16"><path d="M3 10l5-5 5 5" stroke="#fff" stroke-width="2.2" fill="none"/></svg></a>

</body>
</html>
```